Visitenkarten/Briefpaier/Kassenkassenbelege für Juwelier
Zielgruppe
Mittelständischer Juwelier mit zwei Filialen. Klassischer Schmuck, Uhren und Modeschmuck
Aufgabenstellung
Es müssen für zwei Geschäfte Visitenkarten, Briefpapier (A4) und Kassenkassenbelege (A6) erstellt werden. Logo und Typo im Anhang. Ein Farbkonzept besteht noch nicht. Die Idee geht in Richtung Bordeaux-Rot.
Generell:
(1) Sieht erstmal nach viel Beschreibung aus, bitte nicht entmutigen lassen, sind zu 90% nur austauschbare Inhalts-/Kontaktdaten.
(2) Für meine Zwecke reicht es vollkommen aus, wenn bei den Vorschlägen zur Arbeitsersparnis erstmal nur mit einer Adresse gearbeitet wird. Wenn ich dann den zutreffenden Designvorschlag gefunden habe, können wir die zweite Adresse in dem ersten Format umsetzen. Ich denke das spart Zeit und Nerven.
(3) Bitte Angaben wie "Tel.:" oder "USt.- ID:" nicht wörtlich nehmen, es soll dabei klar sein worum es geht; wenn "Telefon" ausgeschrieben besser aussieht, bitte in der optisch ansprechenderen Form verwenden.
(4) Bei Fragen, bitte fragen!
(5) Viel Spass bei dem Projekt - Ich freu' mich auf die Vorschläge!
Visitenkarten(1):
Juwelier Brenneck GmbH
www.juwelier-brenneck-beispiel.de
Visitenkarten(2):
Visitenkarten(generell):
(1) Die einzelnen Daten können durch Hervorhebungen wie Adresse, Kontakt, Online/Internet unterteilt bzw. hervorgehoben werden.
(2) Die Visitenkarten sollen farbig gedruckt werden; geplant ist weiß als Hintergrund ist aber nicht zwingend bei einer guten anderen Idee
Briefpapier:
(1)Absender im Adressfeld für DIN-lang Briefumschläge mit Fenster:
(2)Informationen im Footer/Seitenbereich:
Juwelier Brenneck Gmb..

```html
<!DOCTYPE html>
<html lang="de">
<head>
<meta charset="utf-8">
<title>Juwelier Brenneck – Visitenkarte</title>
<link rel="stylesheet" href="https://fonts.googleapis.com/css2?family=Source+Sans+3:wght@400;600&display=swap">
<style>
  :root {
    --stage: #3a0508;
    --bordeaux: #7c0f14;
    --bordeaux-deep: #5e0a0e;
    --bordeaux-stripe: #6a0c11;
    --gold: #e6d7b0;
    --gold-soft: #d9c79b;
    --gold-band: #efe3c2;
  }
  * { box-sizing: border-box; margin: 0; padding: 0; }
  html, body { width: 1200px; height: 1200px; overflow: hidden; }
  body {
    background: var(--stage);
    font-family: "Source Sans 3", sans-serif;
    color: var(--gold);
    display: flex;
    flex-direction: column;
    align-items: center;
    justify-content: center;
    gap: 60px;
  }
  .card {
    width: 760px;
    height: 492px;
    background: var(--bordeaux);
    position: relative;
    overflow: hidden;
  }
  /* front */
  .card-front .brand-band {
    position: absolute;
    left: 50%;
    top: 0;
    width: 78px;
    height: 150px;
    transform: translateX(-50%);
    background: linear-gradient(90deg, var(--gold-soft), var(--gold-band), var(--gold-soft));
  }
  .brand-name {
    font-weight: 600;
    text-transform: uppercase;
    letter-spacing: 0.06em;
    color: var(--gold);
    white-space: nowrap;
  }
  .card-front .brand-name {
    position: absolute;
    left: 0; right: 0;
    top: 200px;
    text-align: center;
    font-size: 50px;
  }
  .card-front .brand-rule {
    position: absolute;
    top: 290px;
    height: 2px;
    width: 190px;
    background: var(--gold);
  }
  .card-front .brand-rule.left { left: 130px; }
  .card-front .brand-rule.right { right: 130px; }

  /* back */
  .card-back { display: flex; }
  .panel-address {
    width: 57%;
    position: relative;
    border-right: 3px solid var(--gold-soft);
  }
  .panel-address .brand-band {
    position: absolute;
    left: 50%;
    top: 0;
    width: 60px;
    height: 95px;
    transform: translateX(-50%);
    background: linear-gradient(90deg, var(--gold-soft), var(--gold-band), var(--gold-soft));
  }
  .panel-address .brand-name {
    position: absolute;
    left: 0; right: 0;
    top: 130px;
    text-align: center;
    font-size: 31px;
  }
  .panel-address .brand-rule {
    position: absolute;
    top: 188px;
    left: 60px;
    right: 60px;
    height: 2px;
    background: var(--gold);
  }
  .address {
    position: absolute;
    left: 0; right: 0;
    top: 245px;
    text-align: center;
    font-size: 21px;
    line-height: 1.45;
    color: var(--gold-soft);
  }
  .panel-contact {
    flex: 1;
    position: relative;
    background: linear-gradient(135deg, var(--bordeaux-stripe), var(--bordeaux-deep));
  }
  .ornament {
    position: absolute;
    left: 80px;
    top: 40px;
    width: 150px;
    height: 130px;
    border-radius: 70px 70px 10px 70px;
    background: var(--gold-soft);
    opacity: 0.85;
  }
  .contact-phone {
    position: absolute;
    left: 0; right: 0;
    top: 225px;
    text-align: center;
    font-size: 20px;
    line-height: 1.45;
    color: var(--gold-soft);
  }
  .contact-online {
    position: absolute;
    left: 0; right: 0;
    top: 370px;
    text-align: center;
    font-size: 17px;
    line-height: 1.5;
    color: var(--gold-soft);
  }
</style>
</head>
<body>
  <section class="card card-front" aria-label="Visitenkarte Vorderseite">
    <div class="brand-band"></div>
    <div class="brand-name">Juwelier Brenneck</div>
    <div class="brand-rule left"></div>
    <div class="brand-rule right"></div>
  </section>

  <section class="card card-back" aria-label="Visitenkarte Rückseite">
    <div class="panel-address">
      <div class="brand-band"></div>
      <div class="brand-name">Juwelier Brenneck</div>
      <div class="brand-rule"></div>
      <p class="address">
        Juwelier Brenneck GmbH<br>
        Goldschmiedgasse 12<br>
        45000 Musterstadt
      </p>
    </div>
    <div class="panel-contact">
      <div class="ornament" role="img" aria-label="Goldenes geschwungenes Zierornament"></div>
      <p class="contact-phone">
        Tel.: 0000 - 12 34 56<br>
        Fax: 0000 - 12 34 57
      </p>
      <p class="contact-online">
        info@juwelier-brenneck-beispiel.de<br>
        www.juwelier-brenneck-beispiel.de
      </p>
    </div>
  </section>
</body>
</html>
```